Corvane Capital Business Cards

These are professional business cards that are for my family office.
Put fake emails and phone numbers as of now until I finalize those components. This family office controls my families investments, assets, and future. The cards should be professional.
..
.
.
.
I just uploaded another variation of a logo I would like to see as a business card to I am inbeteen which logo to use

Target Market(s)

business

Industry/Entity Type

business

Contact Information for Business Card

Professional, wealth related, finance related.

Requirements
Must have
• Logo

```html
<!DOCTYPE html>
<html lang="en">
<head>
<meta charset="utf-8">
<title>Corvane Capital Business Cards</title>
<link href="https://fonts.googleapis.com/css2?family=Cinzel:wght@400;600;700&display=swap" rel="stylesheet">
<style>
  :root {
    --navy: #1b2030;
    --paper: #ffffff;
    --backdrop: #3b3b3d;
    --ink: #1b2030;
  }
  * { box-sizing: border-box; margin: 0; padding: 0; }
  html, body { width: 1200px; height: 1059px; overflow: hidden; }
  body {
    background: var(--backdrop);
    font-family: "Cinzel", "Times New Roman", serif;
    position: relative;
  }
  .card {
    position: absolute;
    border-radius: 24px;
    overflow: hidden;
    box-shadow: 6px 10px 18px rgba(0,0,0,0.45);
  }
  .card--front { left: 256px; top: 100px; width: 688px; height: 392px; background: var(--paper); color: var(--ink); }
  .card--back { left: 253px; top: 536px; width: 694px; height: 396px; background: var(--navy); color: var(--paper); }

  .details { position: absolute; left: 0; top: 0; width: 350px; height: 100%; text-align: center; }
  .details > * { position: absolute; left: 0; width: 100%; white-space: nowrap; }
  .company-small { top: 30px; font-size: 31px; font-weight: 600; letter-spacing: 0.5px; }
  .person-name { top: 95px; font-size: 29px; font-weight: 600; letter-spacing: 0.5px; }
  .person-title { top: 137px; font-size: 17px; letter-spacing: 1px; }
  .contact-row { top: 175px; height: 28px; }
  .contact-row .rule { position: absolute; top: 13px; height: 2px; background: var(--ink); width: 63px; }
  .contact-row .rule--left { left: 60px; }
  .contact-row .rule--right { left: 227px; }
  .icons { position: absolute; left: 130px; top: 0; display: flex; gap: 4px; }
  .icon { width: 27px; height: 27px; background: var(--ink); border-radius: 6px; display: flex; align-items: center; justify-content: center; }
  .phone { top: 220px; font-size: 18px; }
  .email { top: 248px; font-size: 17px; letter-spacing: 0.5px; }
  .website { top: 276px; font-size: 17px; letter-spacing: 0.3px; }
  .divider { top: 306px; left: 72px !important; width: 205px !important; height: 2px; background: var(--ink); }
  .address { top: 322px; font-size: 17px; line-height: 27px; }

  .mark-ring { position: absolute; border-radius: 50%; }
  .card--front .mark-ring { left: 420px; top: 23px; width: 268px; height: 268px; border: 4px solid var(--ink); }
  .company-large { position: absolute; left: 318px; top: 326px; font-size: 40px; font-weight: 600; white-space: nowrap; line-height: 1; }

  .card--back .mark-ring { left: 243px; top: 62px; width: 212px; height: 212px; border: 4px solid var(--paper); }
  .company-back { position: absolute; left: 0; width: 100%; top: 298px; text-align: center; font-size: 39px; font-weight: 600; line-height: 1; white-space: nowrap; }
</style>
</head>
<body>
  <section class="card card--front" aria-label="Business card front">
    <div class="details">
      <div class="company-small">Corvane Capital</div>
      <div class="person-name">DANIEL HARTLEY</div>
      <div class="person-title">Managing Director</div>
      <div class="contact-row">
        <span class="rule rule--left"></span>
        <div class="icons">
          <span class="icon"><svg width="17" height="17" viewBox="0 0 24 24"><path fill="#fff" d="M6.6 10.8a15 15 0 0 0 6.6 6.6l2.2-2.2c.3-.3.7-.4 1-.2 1.1.4 2.3.6 3.6.6.6 0 1 .4 1 1V20c0 .6-.4 1-1 1C10.6 21 3 13.4 3 4c0-.6.4-1 1-1h3.5c.6 0 1 .4 1 1 0 1.3.2 2.5.6 3.6.1.3 0 .7-.2 1z"/></svg></span>
          <span class="icon"><svg width="17" height="17" viewBox="0 0 24 24"><rect x="3" y="5" width="18" height="14" rx="2" fill="#fff"/><path d="M3.5 6l8.5 7 8.5-7" fill="none" stroke="#1b2030" stroke-width="2"/></svg></span>
          <span class="icon"><svg width="17" height="17" viewBox="0 0 24 24"><circle cx="12" cy="12" r="9" fill="#fff"/><path d="M3 12h18M12 3c3 3 3 15 0 18M12 3c-3 3-3 15 0 18" fill="none" stroke="#1b2030" stroke-width="1.5"/></svg></span>
        </div>
        <span class="rule rule--right"></span>
      </div>
      <div class="phone">123 456 789</div>
      <div class="email">INFO@YOURMAIL.COM</div>
      <div class="website">WWW.YOURWEBSITE.COM</div>
      <div class="divider"></div>
      <div class="address">Your address, City<br>State, Zip 1234</div>
    </div>
    <div class="mark-ring" aria-hidden="true"></div>
    <div class="company-large">Corvane Capital</div>
  </section>

  <section class="card card--back" aria-label="Business card back">
    <div class="mark-ring" aria-hidden="true"></div>
    <div class="company-back">Corvane Capital</div>
  </section>
</body>
</html>
```